Halvex Power

We need a business card for "Halvex power". I have uploaded the logo, the color of the card should be according to the logo "Blackish".
Basically halvex power is a solar company.
Also we would like a sample file in which we can edit the information such names and contact details ourselves
The card would be two sided with following details
1- logo on front and underneath the logo there should be a line saying
"Cleaner . Cheaper . Power"
2-website i.e "www.halvexpowerco.com"
3- Icons for Facebook and Instagram that tells the clients we are available on both social sites.
4- name of the person with his/her designation underneath and email address
5-contact number
6- 1-800--- number with the extension number

its up to the designer how he/she places the details,but it must look professional

Industry/Entity Type

Business

Contact Information for Business Card

5-contact number

Requirements
Must have
• 1- logo on front and underneath the logo there should be a line saying
• "Cleaner . Cheaper . Power"
• 2-website i.e "www.halvexpowerco.com"
• 3- Icons for Facebook and Instagram that tells the clients we are available on both social sites.
• 4- name of the person with his/her designation underneath and email address
• 5-contact number of the person
• 6- 1-800--- number with the extension number
• 7-card should be in black shade like the logo

```html
<!DOCTYPE html>
<html lang="en">
<head>
<meta charset="utf-8">
<title>Halvex Power – Business Card</title>
<link rel="stylesheet" href="https://fonts.googleapis.com/css2?family=Montserrat:wght@600;700&family=Open+Sans:wght@300;400&display=swap">
<style>
  :root {
    --page: #e9e8e4;
    --card-deep: #141c28;
    --card-mid: #1f2a3a;
    --card-light: #34445a;
    --accent: #7cc63a;
    --ink: #eef2f6;
    --ink-soft: #c9d2dc;
  }
  * { box-sizing: border-box; margin: 0; padding: 0; }
  html, body { width: 1200px; height: 930px; overflow: hidden; background: var(--page); }
  .sheet {
    width: 1200px; height: 930px;
    display: flex; flex-direction: column; align-items: center; justify-content: center; gap: 34px;
  }
  .card {
    position: relative; width: 760px; height: 434px; border-radius: 16px; overflow: hidden;
    background: linear-gradient(100deg, var(--card-deep) 0%, var(--card-mid) 45%, var(--card-mid) 100%);
    box-shadow: 0 10px 28px rgba(0,0,0,.25);
  }
  .card__photo {
    position: absolute; top: 0; right: 0; width: 60%; height: 100%;
    background: linear-gradient(160deg, var(--card-light) 0%, #2a384b 50%, var(--card-mid) 100%);
    opacity: .85;
  }
  .card__photo::before {
    content: ""; position: absolute; inset: 0;
    background: linear-gradient(90deg, var(--card-mid) 0%, rgba(31,42,58,0) 40%);
  }
  .brand {
    display: flex; align-items: center; gap: 14px; white-space: nowrap;
    font-family: "Montserrat", sans-serif; font-weight: 700; color: var(--accent);
  }
  .brand__dot { border-radius: 50%; background: var(--accent); flex: none; }

  .front-stack {
    position: absolute; inset: 0;
    display: flex; flex-direction: column; align-items: center; justify-content: center;
  }
  .card--front .brand { font-size: 46px; line-height: 1; }
  .card--front .brand__dot { width: 50px; height: 50px; }
  .tagline {
    margin-top: 18px; font-family: "Open Sans", sans-serif; font-weight: 400;
    font-size: 17px; letter-spacing: 3px; color: var(--ink); white-space: nowrap;
  }
  .social { display: flex; gap: 14px; margin-top: 30px; }
  .social__slot { width: 22px; height: 22px; border-radius: 4px; background: var(--ink); }

  .card--back .brand { position: absolute; left: 50px; top: 266px; font-size: 30px; line-height: 1; }
  .card--back .brand__dot { width: 34px; height: 34px; }
  .divider { position: absolute; left: 360px; top: 100px; width: 2px; height: 250px; background: var(--ink); }
  .details { position: absolute; left: 390px; top: 92px; font-family: "Open Sans", sans-serif; font-weight: 300; color: var(--ink-soft); }
  .details__name { font-family: "Montserrat", sans-serif; font-weight: 700; font-size: 32px; line-height: 1.2; color: var(--accent); letter-spacing: .5px; }
  .details__role { font-size: 17px; margin-top: 2px; margin-bottom: 14px; color: var(--ink); }
  .details__line { font-size: 16px; line-height: 25px; }
  .contact { list-style: none; margin-top: 10px; }
  .contact li { display: flex; align-items: center; gap: 12px; font-size: 16px; line-height: 27px; white-space: nowrap; }
  .contact svg { width: 14px; height: 14px; flex: none; }
</style>
</head>
<body>
<main class="sheet">
  <section class="card card--front" aria-label="Card front">
    <div class="card__photo" role="img" aria-label="Muted photo of a modern office interior"></div>
    <div class="front-stack">
      <div class="brand"><span class="brand__dot"></span>Halvex Power</div>
      <p class="tagline">Cleaner . Cheaper . Power</p>
      <div class="social" aria-label="Social media">
        <span class="social__slot" aria-label="Facebook"></span>
        <span class="social__slot" aria-label="Instagram"></span>
      </div>
    </div>
  </section>

  <section class="card card--back" aria-label="Card back">
    <div class="card__photo" role="img" aria-label="Muted photo of a modern office interior"></div>
    <div class="brand"><span class="brand__dot"></span>Halvex Power</div>
    <div class="divider"></div>
    <div class="details">
      <h1 class="details__name">MARTEN COLE</h1>
      <p class="details__role">President</p>
      <p class="details__line">14 Ridgeline Commerce Way</p>
      <p class="details__line">Stonebrook Park R2K 4T8</p>
      <ul class="contact">
        <li>
          <svg viewBox="0 0 16 16" aria-hidden="true"><path fill="#7cc63a" d="M3 1l3 3-2 2c1 2 3 4 5 5l2-2 3 3-2 3C7 15 1 9 1 3z"/></svg>
          1-800-555-0142 Ext. 204
        </li>
        <li>
          <svg viewBox="0 0 16 16" aria-hidden="true"><rect x="4" y="1" width="8" height="14" rx="1.5" fill="none" stroke="#7cc63a" stroke-width="1.6"/><circle cx="8" cy="12.3" r="1" fill="#7cc63a"/></svg>
          1-833-555-0178
        </li>
        <li>
          <svg viewBox="0 0 16 16" aria-hidden="true"><rect x="1" y="3" width="14" height="10" rx="1" fill="none" stroke="#7cc63a" stroke-width="1.6"/><path d="M1.5 3.5L8 9l6.5-5.5" fill="none" stroke="#7cc63a" stroke-width="1.6"/></svg>
          info@halvexpowerco.com
        </li>
        <li>
          <svg viewBox="0 0 16 16" aria-hidden="true"><circle cx="8" cy="8" r="6.5" fill="none" stroke="#7cc63a" stroke-width="1.5"/><ellipse cx="8" cy="8" rx="3" ry="6.5" fill="none" stroke="#7cc63a" stroke-width="1.2"/><path d="M1.5 8h13" stroke="#7cc63a" stroke-width="1.2"/></svg>
          www.halvexpowerco.com
        </li>
      </ul>
    </div>
  </section>
</main>
</body>
</html>
```